Halvik - consultancy website

I need a new design for my webpage/presence [to be functioning with Wordpress - I have a programmer to set it up but not the design idea].
My company is Halvik - a consultancy firm focused on growth management for Swedish SME's primarily;. We call it Leadership toolkit for firms on the rise, kind of a doctor helping small become big. Contentwise, its a simple frontpage + 3-4 subpages with content re company/myself/focus etc. The new site should communicate a fresh, trustworthy take yet simple and functional on all devices [i.e. think UI compatible for mobile/tablet]. Current building parts/form elements are
a) existing logo and text elements
b) existing pictures
c) the yellowish color
colours and new ideas on pictures/positioning are welcome. I prefer a 'full width page' solution with centralised text elements but that's all up to you to suggest. Current site is a quickfix made by myself - now I'm moving it to a new platform so want to take the opportunity to make it
Nothing superspecial as it is a 2-man show; on the other hand I still want to have a modern & fresh reflection of my brand in digital environments. Help me out!
www.halvik-demo.se
Best
Lina Bergqvist

```html
<!DOCTYPE html>
<html lang="en">
<head>
<meta charset="utf-8">
<title>Halvik – What H do</title>
<link rel="stylesheet" href="https://fonts.googleapis.com/css2?family=Bitter:wght@400;500&display=swap">
<style>
:root{
  --ink:#333333;
  --text:#444444;
  --accent:#ec9b2a;
  --green:#6aa741;
  --sky:#1e8fe0;
  --sky-light:#5fb6ef;
  --wall:#ececec;
  --yellow:#fdd21d;
  --footer:#383838;
  --white:#ffffff;
}
*{box-sizing:border-box;margin:0;padding:0}
html,body{width:1200px;height:1089px;overflow:hidden;background:var(--white)}
body{font-family:"Bitter",Georgia,serif;color:var(--text);position:relative}

.site-header{position:absolute;left:0;top:0;width:1200px;height:103px;
  background:linear-gradient(#ffffff,#f2f1f2)}
.brand{position:absolute;left:74px;top:18px;font-size:58px;font-weight:400;color:var(--ink);letter-spacing:-0.5px}
.main-nav{position:absolute;right:74px;top:54px;display:flex;gap:50px}
.main-nav a{font-size:17px;color:var(--ink);text-decoration:none;position:relative;padding:0 8px}
.main-nav a.is-active{color:var(--accent)}
.main-nav a.is-active::after{content:"";position:absolute;left:0;right:0;top:26px;height:2px;background:var(--accent)}

.hero{position:absolute;left:75px;top:148px;display:flex;gap:17px}
.tile{width:339px;height:321px}
.tile--pitch{background:var(--green);color:var(--white);text-align:right;padding:38px 34px 0 20px;font-size:23px;line-height:31px}
.tile--pitch .cta{display:block;margin-top:25px;padding-right:6px;font-size:22px}
.tile--kite{background:linear-gradient(160deg,var(--sky-light),var(--sky) 60%,#0c6fc4)}
.tile--growth{background:linear-gradient(#f4f4f4,var(--wall))}

.intro{position:absolute;left:74px;top:535px;width:1050px}
.intro h1{font-size:24px;font-weight:400;color:var(--ink);letter-spacing:0.3px;margin-bottom:16px}
.intro p{font-size:14px;line-height:22px;text-align:justify;letter-spacing:0.3px;margin-bottom:22px}
.offer{font-size:17px;line-height:22px;color:#111}
.offer .muted{color:#555}

.services{position:absolute;left:74px;top:806px;width:692px;height:148px;background:var(--accent);
  display:grid;grid-template-columns:323px 1fr;row-gap:13px;padding:26px 0 0 23px;list-style:none}
.services li{display:flex;align-items:center;gap:10px;color:var(--white);font-size:16px;letter-spacing:0.3px}
.services svg{flex:none}

.signup{position:absolute;left:794px;top:806px;width:332px;height:148px;background:var(--yellow)}
.signup .bubble{position:absolute;left:19px;top:16px;width:68px;height:68px;border-radius:50%;background:var(--ink);
  color:var(--white);font-size:12px;line-height:13px;text-align:center;padding-top:22px}
.signup .bubble::after{content:"";position:absolute;left:28px;bottom:-9px;border:6px solid transparent;border-top:8px solid var(--ink);border-bottom:0}
.signup .prompt{position:absolute;left:114px;top:28px;font-size:15px;line-height:22px;color:var(--ink)}
.signup form{position:absolute;left:114px;top:86px;display:flex}
.signup input{width:159px;height:37px;border:0;padding:0 16px;font:13px Arial,Helvetica,sans-serif;color:#888;background:var(--white)}
.signup input::placeholder{color:#888}
.signup button{width:38px;height:37px;border:0;background:var(--accent);display:flex;align-items:center;justify-content:center}

.site-footer{position:absolute;left:0;top:999px;width:1200px;height:90px;background:var(--footer);color:var(--white);font-size:14px}
.site-footer .legal{position:absolute;left:76px;top:25px}
.site-footer .contact{position:absolute;left:76px;top:53px;display:flex;gap:27px}
.social{position:absolute;right:76px;top:33px;display:flex;gap:10px;list-style:none}
.social li{width:31px;height:31px;border-radius:2px}
.social .s1{background:#1da1e4}.social .s2{background:#3b5b9a}.social .s3{background:#dd4b39}.social .s4{background:#3a6b96}
</style>
</head>
<body>
<header class="site-header">
  <div class="brand">Halvik.</div>
  <nav class="main-nav">
    <a href="#">Home</a>
    <a href="#" class="is-active">What H do</a>
    <a href="#">Who H are</a>
    <a href="#">Why H</a>
  </nav>
</header>

<section class="hero">
  <div class="tile tile--pitch">Got momentum to make that leap into next level of business maturity?<span class="cta">PROGRESS FOR HIRE!</span></div>
  <div class="tile tile--kite" role="img" aria-label="Hand holding a colourful kite string against a bright blue sky"></div>
  <div class="tile tile--growth" role="img" aria-label="Child looking up at height marks drawn on a white wall"></div>
</section>

<section class="intro">
  <h1>PROGRESS - JUST IN TIME.</h1>
  <p>Consultancy services aiming to help high-performing organizations adapt to change and evolving economic conditions. H delivers structure, means and orchestration to help growing companies develop healthy – where in-house competencies or bandwidth is simply not enough to implement a qualitative approach and lead on through.</p>
  <p>In brief, an experienced trouble shooting asset when you need it.</p>
  <div class="offer">Growth plans? <span class="muted">Download</span><br><span class="muted">Halvik's</span> Kickstart offer [SWE]</div>
</section>

<ul class="services">
  <li><svg width="20" height="20" viewBox="0 0 20 20"><circle cx="10" cy="10" r="8.5" fill="none" stroke="#fff" stroke-width="2"/><path d="M5.5 10h7M9.5 6.5 13 10l-3.5 3.5" fill="none" stroke="#fff" stroke-width="2"/></svg>Growth management</li>
  <li><svg width="20" height="20" viewBox="0 0 20 20"><circle cx="10" cy="10" r="8.5" fill="none" stroke="#fff" stroke-width="2"/><path d="M5.5 10h7M9.5 6.5 13 10l-3.5 3.5" fill="none" stroke="#fff" stroke-width="2"/></svg>Gap analysis &amp; field research papers</li>
  <li><svg width="20" height="20" viewBox="0 0 20 20"><circle cx="10" cy="10" r="8.5" fill="none" stroke="#fff" stroke-width="2"/><path d="M5.5 10h7M9.5 6.5 13 10l-3.5 3.5" fill="none" stroke="#fff" stroke-width="2"/></svg>Corporate communications</li>
  <li><svg width="20" height="20" viewBox="0 0 20 20"><circle cx="10" cy="10" r="8.5" fill="none" stroke="#fff" stroke-width="2"/><path d="M5.5 10h7M9.5 6.5 13 10l-3.5 3.5" fill="none" stroke="#fff" stroke-width="2"/></svg>Project management</li>
  <li><svg width="20" height="20" viewBox="0 0 20 20"><circle cx="10" cy="10" r="8.5" fill="none" stroke="#fff" stroke-width="2"/><path d="M5.5 10h7M9.5 6.5 13 10l-3.5 3.5" fill="none" stroke="#fff" stroke-width="2"/></svg>Organizational development</li>
  <li><svg width="20" height="20" viewBox="0 0 20 20"><circle cx="10" cy="10" r="8.5" fill="none" stroke="#fff" stroke-width="2"/><path d="M5.5 10h7M9.5 6.5 13 10l-3.5 3.5" fill="none" stroke="#fff" stroke-width="2"/></svg>Conceptualizing</li>
</ul>

<aside class="signup">
  <div class="bubble">Get in<br>touch</div>
  <p class="prompt">Simply drop your Email<br>here...</p>
  <form>
    <input type="email" placeholder="Enter Email">
    <button type="submit" aria-label="Submit"><svg width="12" height="14" viewBox="0 0 12 14"><path d="M3 2l5 5-5 5" fill="none" stroke="#fff" stroke-width="2.5"/></svg></button>
  </form>
</aside>

<footer class="site-footer">
  <div class="legal">Halvik © 2015 | Privacy Policy</div>
  <div class="contact"><span>T: +46 [0] 700 12 34 56</span><span>E: info@halvik-demo.se</span></div>
  <ul class="social" aria-label="Social links">
    <li class="s1"></li><li class="s2"></li><li class="s3"></li><li class="s4"></li>
  </ul>
</footer>
</body>
</html>
```